We are a building company that build new homes and units we are looking for something fresh and looks good my company name is
Lark Building Co Pty Ltd

Industry/Entity Type

Building

Contact Information for Business Card

Name Marco Ellis-Dunford
Tittle: Director
Address 14 Corrin St. Pelham Vale Vic 3179
Ph: 03 9582 4063
Mobile : 0400 362 918

www.larkbuildingco.com.au
Email: sales@larkbuildingco.com.au

```html
<!DOCTYPE html>
<html lang="en">
<head>
<meta charset="utf-8">
<title>Lark Building Co Pty Ltd — Business Card</title>
<link rel="stylesheet" href="https://fonts.googleapis.com/css2?family=Open+Sans:wght@400;600;700&display=swap">
<style>
  :root {
    --backdrop: #d7d8da;
    --card-black: #0b0b0c;
    --card-white: #ffffff;
    --brand-blue: #1f78c8;
    --name-grey: #4a4a4a;
    --text-dark: #2b2b2b;
    --wordmark: #d6dbe1;
    --card-w: 640px;
    --card-h: 366px;
  }
  * { box-sizing: border-box; margin: 0; padding: 0; }
  html, body {
    width: 1200px; height: 900px; overflow: hidden;
    background: var(--backdrop);
    font-family: "Open Sans", Arial, sans-serif;
  }
  .stage {
    width: 1200px; height: 900px;
    display: flex; flex-direction: column; align-items: center; justify-content: center;
    gap: 56px;
  }
  .card {
    position: relative;
    width: var(--card-w); height: var(--card-h);
    background: var(--card-black);
    box-shadow: 0 10px 28px rgba(0,0,0,.25);
    overflow: hidden;
  }
  .wordmark {
    color: var(--wordmark);
    font-weight: 600;
    text-align: center;
    line-height: 1.15;
    display: flex; align-items: center; gap: 12px;
  }
  .wordmark__mark {
    width: 14px; height: 14px; background: var(--brand-blue); flex: none;
  }
  .card--back { display: flex; align-items: center; justify-content: center; }
  .card--back .wordmark { font-size: 30px; }

  .card--front .info-panel {
    position: absolute; left: 0; top: 0; bottom: 0;
    width: 332px;
    background: var(--card-white);
    clip-path: polygon(0 0, 300px 0, 300px 62px, 318px 76px, 300px 90px, 300px 100%, 0 100%);
    padding: 60px 0 0 34px;
  }
  .card--front .brand-side {
    position: absolute; left: 300px; right: 0; top: 0; bottom: 0;
    display: flex; align-items: center; justify-content: center;
  }
  .card--front .wordmark { font-size: 24px; }
  .person-name { font-size: 21px; font-weight: 400; color: var(--name-grey); white-space: nowrap; }
  .person-name__first { color: var(--brand-blue); }
  .person-title { font-size: 13px; font-weight: 700; color: var(--text-dark); margin-top: 6px; }
  .contact-list { list-style: none; margin-top: 52px; }
  .contact-list li {
    display: flex; align-items: center; gap: 9px;
    font-size: 15.5px; color: var(--text-dark); font-weight: 600;
    margin-bottom: 5px; white-space: nowrap;
  }
  .contact-list li.contact-list__small { font-size: 13.5px; }
  .contact-list svg { width: 13px; height: 13px; fill: var(--text-dark); flex: none; }
</style>
</head>
<body>
<main class="stage">
  <section class="card card--back" aria-label="Card back">
    <div class="wordmark"><span class="wordmark__mark"></span><span>Lark Building Co<br>Pty Ltd</span></div>
  </section>

  <section class="card card--front" aria-label="Card front">
    <div class="info-panel">
      <p class="person-name"><span class="person-name__first">Marco</span> Ellis-Dunford</p>
      <p class="person-title">Director</p>
      <ul class="contact-list">
        <li>
          <svg viewBox="0 0 16 16" aria-hidden="true"><path d="M3.5 1l2.5 3-1.5 2c1 2 3 4 5 5l2-1.5 3 2.5-1.5 2.5C8 15 1 8 1 2.5z"/></svg>
          03 9582 4063
        </li>
        <li>
          <svg viewBox="0 0 16 16" aria-hidden="true"><path d="M4 0h8v16H4zM5.5 2v9h5V2zM7 12.5h2v2H7z" fill-rule="evenodd"/></svg>
          0400 362 918
        </li>
        <li class="contact-list__small">
          <svg viewBox="0 0 16 16" aria-hidden="true"><path d="M0 3h16v10H0zM1.5 4.5l6.5 5 6.5-5z" fill-rule="evenodd"/></svg>
          sales@larkbuildingco.com.au
        </li>
        <li class="contact-list__small">
          <svg viewBox="0 0 16 16" aria-hidden="true"><path d="M8 0a8 8 0 110 16A8 8 0 018 0zm0 1.5C6.8 3 6.2 5 6.1 7.2h3.8C9.8 5 9.2 3 8 1.5zM1.6 8.8c.3 2.6 2.2 4.7 4.6 5.4-.9-1.5-1.5-3.4-1.6-5.4zm8.2 0c-.1 2-.7 3.9-1.6 5.4 2.4-.7 4.3-2.8 4.6-5.4zM6.1 8.8c.1 2.2.7 4.2 1.9 5.7 1.2-1.5 1.8-3.5 1.9-5.7zm-1.5-1.6c.1-2 .7-3.9 1.6-5.4-2.4.7-4.3 2.8-4.6 5.4zm6.8 0h3c-.3-2.6-2.2-4.7-4.6-5.4.9 1.5 1.5 3.4 1.6 5.4z"/></svg>
          www.larkbuildingco.com.au
        </li>
        <li class="contact-list__small">
          <svg viewBox="0 0 16 16" aria-hidden="true"><path d="M8 0a5.5 5.5 0 015.5 5.5C13.5 10 8 16 8 16S2.5 10 2.5 5.5A5.5 5.5 0 018 0zm0 3.2a2.3 2.3 0 100 4.6 2.3 2.3 0 000-4.6z" fill-rule="evenodd"/></svg>
          14 Corrin St. Pelham Vale Vic 3179
        </li>
      </ul>
    </div>
    <div class="brand-side">
      <div class="wordmark"><span class="wordmark__mark"></span><span>Lark Building Co<br>Pty Ltd</span></div>
    </div>
  </section>
</main>
</body>
</html>
```